Modern/Bold/Unique Prenatal Vitamin label redesign

We are in need of a design update for our Prenatal Vitamin label. We want to modernize our label and give it a fresh feel.
It should bring a feeling of fun, joy, and sophistication, but also be bold/edgy/unique and portray Trust and Authority. Our buyers are mainly mothers in the age range of 25-34 who are pregnant or breastfeeding.
I will attach our current label design, as well as some inspiration to go off of.
We like the idea of having a clean, easy to read label label with bold/vibrant colors and fonts. We like the idea of having some retro vibes in it as well
Please see the attached artwork for design inspiration (New Design Idea). We like the idea of having a pregnant mother image like the attachment on the label, with the rest of the label being white. Please come up with a unique drawing/image for the design. We cannot use a copied image or stock image.
We look forward to working with you!

```html
<!DOCTYPE html>
<html lang="en">
<head>
<meta charset="UTF-8">
<title>Luna Nest Naturals – Prenatal Glow Label</title>
<link href="https://fonts.googleapis.com/css2?family=Nunito:wght@800;900&family=Yellowtail&display=swap" rel="stylesheet">
<style>
  :root {
    --cream: #fbf3ee;
    --blush: #f3e0d6;
    --peach-band: #efd1bf;
    --orange: #f0a11a;
    --orange-deep: #e8930f;
    --ink: #1d1a19;
    --skin: #eeaa80;
    --sage: #b5cbc0;
    --rose: #e9a092;
  }
  * { margin: 0; padding: 0; box-sizing: border-box; }
  html, body { width: 965px; height: 1200px; overflow: hidden; background: #ffffff; }
  .label {
    position: relative;
    width: 965px;
    height: 1200px;
    background: linear-gradient(90deg, var(--blush) 0%, var(--cream) 30%, var(--cream) 65%, var(--blush) 100%);
    overflow: hidden;
    font-family: "Nunito", sans-serif;
  }
  .top-band { position: absolute; inset: 0 0 auto 0; width: 965px; height: 160px; }
  .art { position: absolute; }
  .floral-left  { left: 0;   top: 55px; width: 340px; height: 230px; border-radius: 0 0 60% 0; background: linear-gradient(135deg, rgba(233,160,146,.55), rgba(181,203,192,.35)); }
  .floral-right { right: 0;  top: 55px; width: 340px; height: 230px; border-radius: 0 0 0 60%; background: linear-gradient(225deg, rgba(233,160,146,.55), rgba(181,203,192,.35)); }
  .hand-left  { left: 40px;  top: 470px; width: 150px; height: 300px; border-radius: 40% 60% 20% 40%; background: linear-gradient(180deg, var(--orange) 0%, var(--skin) 35%, var(--skin) 100%); opacity: .85; }
  .hand-right { right: 40px; top: 470px; width: 150px; height: 300px; border-radius: 60% 40% 40% 20%; background: linear-gradient(180deg, var(--orange) 0%, var(--skin) 35%, var(--skin) 100%); opacity: .85; }
  .mother { left: 290px; top: 655px; width: 290px; height: 445px; border-radius: 45% 45% 30% 30%; background: linear-gradient(180deg, var(--orange) 0%, var(--skin) 25%, var(--sage) 50%, var(--sage) 100%); }
  .leaves-left  { left: 0;  bottom: 10px; width: 130px; height: 150px; border-radius: 0 80% 0 0; background: linear-gradient(160deg, var(--ink), #3a3433); opacity: .9; }
  .leaves-right { right: 0; bottom: 10px; width: 130px; height: 150px; border-radius: 80% 0 0 0; background: linear-gradient(200deg, var(--ink), #3a3433); opacity: .9; }

  .brand { position: absolute; top: 170px; left: 0; width: 965px; text-align: center; color: var(--ink); font-weight: 900; }
  .brand-mark { display: block; width: 96px; height: 96px; margin: 0 auto 18px; border-radius: 50%; background: var(--ink); }
  .brand-name { display: block; font-size: 62px; line-height: 1; letter-spacing: .5px; }
  .brand-sub { display: block; font-size: 44px; line-height: 1.1; letter-spacing: 3px; text-transform: uppercase; }

  .product-title { position: absolute; top: 440px; left: 0; width: 965px; text-align: center; color: var(--orange); font-weight: 900; line-height: .95; }
  .product-title span { display: block; font-size: 122px; letter-spacing: 1px; }

  .script { position: absolute; font-family: "Yellowtail", cursive; color: var(--ink); line-height: 1; }
  .supplement-type { left: 45px; top: 905px; font-size: 56px; text-align: center; transform: rotate(-4deg); }
  .capsule-count { left: 590px; top: 895px; font-size: 54px; text-align: center; transform: rotate(-4deg); }
  .capsule-count .count { display: block; font-size: 74px; }

  .ground-line { position: absolute; left: 225px; top: 1106px; width: 495px; height: 3px; background: var(--ink); }

  .tagline { position: absolute; bottom: 14px; left: 0; width: 965px; text-align: center; color: var(--orange-deep); font-weight: 900; font-size: 34px; line-height: 1.05; text-transform: uppercase; }
</style>
</head>
<body>
  <main class="label">
    <svg class="top-band" viewBox="0 0 965 160" preserveAspectRatio="none" aria-hidden="true">
      <polygon points="0,0 965,0 965,160 0,40" fill="var(--peach-band)" opacity=".7"/>
    </svg>

    <div class="art floral-left" role="img" aria-label="Flowering branch with pink blossoms and small stars"></div>
    <div class="art floral-right" role="img" aria-label="Flowering branch with pink blossoms and small stars"></div>

    <header class="brand">
      <span class="brand-mark"></span>
      <span class="brand-name">Luna Nest</span>
      <span class="brand-sub">Naturals</span>
    </header>

    <div class="art hand-left" role="img" aria-label="Line-drawn open hand reaching upward beneath orange leaves"></div>
    <div class="art hand-right" role="img" aria-label="Line-drawn open hand reaching upward beneath orange leaves"></div>

    <h1 class="product-title"><span>PRENATAL</span><span>GLOW</span></h1>

    <div class="art mother" role="img" aria-label="Illustration of a pregnant woman with flowing hair in a sage dress cradling her belly"></div>
    <div class="ground-line"></div>

    <p class="script supplement-type">Dietary<br>Supplement</p>
    <p class="script capsule-count"><span class="count">90</span>Veggie Capsules</p>

    <div class="art leaves-left" role="img" aria-label="Dark decorative leaves"></div>
    <div class="art leaves-right" role="img" aria-label="Dark decorative leaves"></div>

    <p class="tagline">Once Daily Premium<br>Multivitamin for Mama &amp; Baby</p>
  </main>
</body>
</html>
```